A specialised Sport management needs a corporate brochure design

We are a specialized company in the management and consultancy of sports events. and need to have a company brochure
We provide the following services;
Event management
Venues management
Production
Ticketing
Consulting
Hospitality
Activity management
Event timing
Branding of event
Event supplies
We need a corporate profile design for our company to showcase the major events that we have covered , with images, information, statistics, surveys, products and services used. We want to highlight our professionalism and execution of the events, experience of the participants, spectators . How we have grown in the past few years and reached the international standards.
Objectives of the work:
To get sponsors and partners for future business and to present Tri-Crest
as not just a sports management company but also a professional sports
events management company.
You can check our website
www.tri-crest.example
Target Market(s)
Sponsors and corporate partners
Industry/Entity Type
Events
Requirements
Must have
- Must Have:
- - Very professional look
- -Some event images,Event information, statistics, surveys, products and services used. We want to highlight our professionalism and execution of the events (Attached)
Nice to have
- Similar momentom of the below design
- http://www.lumavent.example/wp-content/themes/lumavent/pdf/CP-2014-15-V10-Web.pdf

```html
<!DOCTYPE html>
<html lang="en">
<head>
<meta charset="utf-8">
<title>Tri-Crest Brochure – Target Segment</title>
<link rel="stylesheet" href="https://fonts.googleapis.com/css2?family=Aldrich&family=Arimo:wght@400;700&family=Oswald:wght@500;600&display=swap">
<style>
  :root {
    --canvas: #e4e4e4;
    --paper: #f1f0ee;
    --paper-shade: #e6e5e2;
    --orange: #f05a28;
    --ink: #3a3a3a;
    --grey-band: #77777a;
    --rule: #2b2b2b;
    --tab-green: #1e8a3c;
    --photo-a: #b9a89a;
    --photo-b: #5f5f66;
  }
  * { box-sizing: border-box; margin: 0; padding: 0; }
  html, body { width: 1200px; height: 799px; overflow: hidden; background: var(--canvas); }
  body { position: relative; font-family: "Arimo", Arial, sans-serif; color: var(--ink); }

  .spread {
    position: absolute; left: 50px; top: 90px; width: 1100px; height: 620px;
    display: flex; box-shadow: 0 6px 18px rgba(0,0,0,.18);
  }
  .page { position: relative; width: 550px; height: 620px; background: var(--paper); overflow: hidden; }
  .page--left { background: linear-gradient(to right, var(--paper) 88%, var(--paper-shade)); }
  .page--right { background: linear-gradient(to left, var(--paper) 88%, var(--paper-shade)); }

  .page-tab {
    position: absolute; width: 18px; height: 8px; background: var(--tab-green);
    color: #fff; font-size: 5px; line-height: 8px; text-align: center;
  }
  .page--left .page-tab { left: 30px; top: 338px; }
  .page--right .page-tab { right: 12px; top: 128px; z-index: 3; }

  .headline {
    position: absolute; left: 50px; top: 180px;
    font-family: "Aldrich", "Arimo", sans-serif; color: var(--orange);
    font-size: 40px; line-height: 38px; letter-spacing: 1px;
  }
  .segment-col { position: absolute; font-size: 10.5px; line-height: 15px; }
  .segment-col h3 { font-size: 11px; font-weight: 700; color: #222; margin-bottom: 4px; }
  .segment-col p { margin-bottom: 16px; }
  .segment-col--a { left: 50px; top: 280px; width: 220px; }
  .segment-col--b { left: 300px; top: 185px; width: 215px; }

  .event-photo { position: absolute; left: 0; bottom: 0; width: 300px; height: 230px; }

  .quote {
    position: absolute; left: 40px; top: 90px; width: 300px;
    font-size: 13px; line-height: 18px; color: #555;
  }
  .quote .mark { color: var(--orange); font-family: "Oswald", sans-serif; font-size: 30px; line-height: 0; vertical-align: -8px; margin-right: 6px; }
  .quote .close { color: var(--orange); }
  .quote-author { position: absolute; left: 40px; top: 132px; font-size: 9px; line-height: 11px; color: var(--orange); }
  .quote-author b { display: block; }

  .stat { position: absolute; top: 175px; width: 125px; }
  .stat-figure { display: flex; align-items: flex-end; gap: 3px; }
  .stat-number { font-family: "Oswald", sans-serif; font-weight: 600; color: var(--orange); font-size: 26px; line-height: 26px; }
  .stat-label { font-size: 7.5px; line-height: 9px; font-weight: 700; color: #222; padding-bottom: 3px; }
  .stat svg { display: block; margin-top: -6px; }
  .stat-rule { height: 1px; background: var(--rule); margin-top: 12px; }
  .stat--1 { left: 40px; } .stat--2 { left: 180px; } .stat--3 { left: 310px; }

  .survey { position: absolute; top: 255px; width: 110px; text-align: center; }
  .survey-ring {
    width: 70px; height: 70px; margin: 0 auto 8px; border-radius: 50%;
    border: 1.5px dashed var(--orange);
    display: flex; align-items: center; justify-content: center;
    font-family: "Oswald", sans-serif; font-weight: 600; color: var(--orange); font-size: 22px;
  }
  .survey p { font-size: 8px; line-height: 10px; color: #555; }
  .survey--1 { left: 48px; } .survey--2 { left: 188px; } .survey--3 { left: 318px; }

  .growth-band { position: absolute; right: 20px; top: 0; width: 92px; height: 620px; background: var(--grey-band); }
  .growth-tag {
    position: absolute; right: 20px; top: 80px; width: 112px; padding: 5px 8px;
    background: var(--orange); color: #fff; font-size: 9px; line-height: 10px; font-weight: 700; text-align: center;
  }
  .timeline-line { position: absolute; right: 62px; top: 125px; width: 1.5px; height: 300px; background: #fff; }
  .timeline-entry { position: absolute; font-size: 7px; line-height: 9px; color: #fff; }
  .timeline-entry b { display: block; font-size: 9px; }
  .timeline-entry--left { right: 68px; text-align: right; }
  .timeline-entry--right { right: 26px; }
</style>
</head>
<body>
  <div class="spread">
    <section class="page page--left">
      <h2 class="headline">TARGET<br>SEGMENT</h2>

      <div class="segment-col segment-col--a">
        <h3>Mainstream Public</h3>
        <p>This is a huge audience reached predominantly through the mainstream print and digital coverage. They are captivated and inspired by the incredible feats of sport events and determination displayed by the athletes. Estimated number of mainstream audience is 50,000.</p>
      </div>

      <div class="segment-col segment-col--b">
        <h3>Engaged</h3>
        <p>This segment encompasses all those who are engaged directly with us, but not necessarily a current athlete.</p>
        <h3>Athletes</h3>
        <p>Majority of athletes are ranging between 20 - 45 years old, %70 Male and %30 Female , with high disposable incomes. They are fit, motivated and looking to challenge themselves.</p>
      </div>

      <span class="page-tab">08</span>

      <svg class="event-photo" viewBox="0 0 300 230" role="img" aria-label="Event photo: athlete lifting a barbell overhead at a competition">
        <defs>
          <linearGradient id="photoTone" x1="0" y1="0" x2="1" y2="1">
            <stop offset="0" stop-color="var(--photo-a)"/>
            <stop offset="1" stop-color="var(--photo-b)"/>
          </linearGradient>
        </defs>
        <polygon points="0,150 110,40 300,230 0,230" fill="url(#photoTone)"/>
        <polygon points="0,150 60,95 150,230 0,230" fill="var(--orange)" opacity=".85"/>
      </svg>
    </section>

    <section class="page page--right">
      <p class="quote"><span class="mark">“</span>Haven't tried any Event managers before Tri-Crest, don't want to try any others<span class="close">”</span></p>
      <p class="quote-author"><b>Nasser Alqadri</b>Founder Ridgeline+</p>

      <div class="stat stat--1">
        <div class="stat-figure"><span class="stat-number">10,000</span><span class="stat-label">Number of<br>participates<br>in 2014</span></div>
        <svg width="40" height="14" viewBox="0 0 40 14"><path d="M1 0V12H36M32 9l4 3-4 3" fill="none" stroke="#222" stroke-width="1.2"/></svg>
        <div class="stat-rule"></div>
      </div>
      <div class="stat stat--2">
        <div class="stat-figure"><span class="stat-number">13</span><span class="stat-label">Number of<br>sports</span></div>
        <svg width="40" height="14" viewBox="0 0 40 14"><path d="M1 0V12H36M32 9l4 3-4 3" fill="none" stroke="#222" stroke-width="1.2"/></svg>
        <div class="stat-rule"></div>
      </div>
      <div class="stat stat--3">
        <div class="stat-figure"><span class="stat-number">+30,000</span><span class="stat-label">Visitors</span></div>
        <svg width="40" height="14" viewBox="0 0 40 14"><path d="M1 0V12H36M32 9l4 3-4 3" fill="none" stroke="#222" stroke-width="1.2"/></svg>
        <div class="stat-rule"></div>
      </div>

      <div class="survey survey--1"><div class="survey-ring">86%</div><p>Said they would rate our events as "Excellent" in our survey (average)</p></div>
      <div class="survey survey--2"><div class="survey-ring">84%</div><p>Said they would participate again (average)</p></div>
      <div class="survey survey--3"><div class="survey-ring">80%</div><p>Said they recognized our sponsors (average)</p></div>

      <div class="growth-band"></div>
      <div class="growth-tag">Growth<br>Over the Years</div>
      <span class="page-tab">09</span>
      <div class="timeline-line"></div>
      <p class="timeline-entry timeline-entry--left" style="top:140px"><b>2014</b>Participants<br>10,000+</p>
      <p class="timeline-entry timeline-entry--right" style="top:205px"><b>2013</b>Participants<br>5,800+</p>
      <p class="timeline-entry timeline-entry--left" style="top:270px"><b>2012</b>Participants<br>2,700</p>
      <p class="timeline-entry timeline-entry--right" style="top:335px"><b>2011</b>Participants<br>1,300</p>
    </section>
  </div>
</body>
</html>
```